Silver Meadow LLC business card

I help with the Marketing and Sales of various Natural, Organic, Eco Friendly and Healthy Main Stream products to Retail Corporate accounts as well as Independents and Distributors.I also highlight Private label items to these same Retail Corporate accounts.Cherish the Moments, Enjoy Life!

Speciality & Health Sales and Marketing

Target Market(s)

Men and Women

Industry/Entity Type

Business

Contact Information for Business Card

Silver Meadow, LLC
Janet Louise Verhagen
438 West Finch Lane
Ste 4-237
Phoenix, AZ 85047
602-555-0147
jverhagen@plumvale.net

Requirements
Must have
• Nice, femine font
Something in the background or on a side with a softness
Nice to have
• Cherish the Moments, Enjoy Life
Should not have
• Hardness

```html
<!DOCTYPE html>
<html lang="en">
<head>
<meta charset="utf-8">
<title>Silver Meadow LLC – Business Card</title>
<link rel="stylesheet" href="https://fonts.googleapis.com/css2?family=Cormorant+Garamond:ital,wght@0,600;1,600&family=Quicksand:wght@400;500&display=swap">
<style>
  :root {
    --orange: #f0692a;
    --orange-soft: #f6925e;
    --charcoal: #2b2624;
    --white: #ffffff;
    --cream: #fbeee4;
    --backdrop: #dcdad8;
  }
  * { box-sizing: border-box; margin: 0; padding: 0; }
  html, body { width: 1200px; height: 900px; overflow: hidden; }
  body {
    background: var(--backdrop);
    font-family: "Quicksand", Arial, sans-serif;
    position: relative;
  }
  .card {
    position: absolute;
    overflow: hidden;
    border-radius: 14px;
    background: linear-gradient(160deg, var(--orange-soft) 0%, var(--orange) 55%);
    box-shadow: 0 8px 22px rgba(60, 40, 30, .18);
  }
  .card-shapes { position: absolute; inset: 0; width: 100%; height: 100%; }
  .card-shapes path { fill: var(--charcoal); }
  .brand-name {
    font-family: "Cormorant Garamond", Georgia, serif;
    font-weight: 600;
    color: var(--white);
    letter-spacing: 1px;
    white-space: nowrap;
  }

  /* Front */
  .card-front { left: 520px; top: 90px; width: 580px; height: 330px; }
  .card-front .mark-zone {
    position: absolute; left: 0; top: 22px; width: 100%;
    display: flex; justify-content: center;
  }
  .card-front .mark-dot {
    width: 88px; height: 88px; border-radius: 50%; background: var(--cream);
  }
  .card-front .brand-name {
    position: absolute; left: 0; top: 168px; width: 100%;
    text-align: center; font-size: 50px; line-height: 60px;
  }

  /* Back */
  .card-back { left: 110px; top: 420px; width: 660px; height: 376px; }
  .card-back .brand-row {
    position: absolute; left: 0; top: 22px; width: 100%;
    display: flex; align-items: center; justify-content: center; gap: 18px;
  }
  .card-back .mark-dot {
    width: 54px; height: 54px; border-radius: 50%; background: var(--orange);
  }
  .card-back .brand-name { font-size: 42px; line-height: 54px; }
  .person {
    position: absolute; left: 34px; top: 124px; color: var(--white);
  }
  .person-name {
    font-family: "Cormorant Garamond", Georgia, serif;
    font-style: italic; font-weight: 600; font-size: 32px; line-height: 1.05;
  }
  .person-title { font-size: 15px; font-weight: 500; letter-spacing: .5px; }
  .contact-list {
    position: absolute; right: 30px; top: 198px;
    list-style: none; color: var(--white);
    font-size: 17px; font-weight: 500; line-height: 27px;
  }
  .contact-list li {
    display: flex; justify-content: flex-end; align-items: center; gap: 10px;
    white-space: nowrap;
  }
  .contact-list svg { width: 15px; height: 15px; fill: var(--white); flex: none; }
</style>
</head>
<body>

  <section class="card card-front" aria-label="Business card front">
    <svg class="card-shapes" viewBox="0 0 580 330" preserveAspectRatio="none" aria-hidden="true">
      <path d="M0 140 Q290 112 580 140 V262 Q290 292 0 262 Z"/>
    </svg>
    <div class="mark-zone"><span class="mark-dot"></span></div>
    <p class="brand-name">Silver Meadow LLC</p>
  </section>

  <section class="card card-back" aria-label="Business card back">
    <svg class="card-shapes" viewBox="0 0 660 376" preserveAspectRatio="none" aria-hidden="true">
      <path d="M0 0 H660 V94 Q330 124 0 94 Z"/>
      <path d="M0 342 Q330 318 660 342 V376 H0 Z"/>
    </svg>

    <div class="brand-row">
      <span class="mark-dot"></span>
      <span class="brand-name">Silver Meadow LLC</span>
    </div>

    <div class="person">
      <p class="person-name">Janet Louise Verhagen</p>
      <p class="person-title">Managing Director</p>
    </div>

    <ul class="contact-list">
      <li>602-555-0147
        <svg viewBox="0 0 16 16" aria-hidden="true"><path d="M3 1h3l1 4-2 1a9 9 0 0 0 5 5l1-2 4 1v3a2 2 0 0 1-2 2A13 13 0 0 1 1 3a2 2 0 0 1 2-2z"/></svg></li>
      <li>jverhagen@plumvale.net
        <svg viewBox="0 0 16 16" aria-hidden="true"><rect x="1" y="3" width="14" height="10" rx="2"/><path d="M2 4l6 5 6-5" fill="none" stroke="#f0692a" stroke-width="1.5"/></svg></li>
      <li>www.silvermeadow.net
        <svg viewBox="0 0 16 16" aria-hidden="true"><path d="M6.5 9.5l3-3M7 4l1.5-1.5a3 3 0 0 1 4 4L11 8M9 12l-1.5 1.5a3 3 0 0 1-4-4L5 8" fill="none" stroke="#fff" stroke-width="2" stroke-linecap="round"/></svg></li>
      <li>438 West Finch Lane, Ste 4-237, Phoenix, AZ 85047
        <svg viewBox="0 0 16 16" aria-hidden="true"><path d="M8 1a5 5 0 0 1 5 5c0 4-5 9-5 9S3 10 3 6a5 5 0 0 1 5-5z"/><circle cx="8" cy="6" r="2" fill="#f0692a"/></svg></li>
    </ul>
  </section>

</body>
</html>
```